New Business Card Design Project

Use the flyer uploaded and website www.brightoakbuilders.com for inspiration.
List Our Services on Backside of business cards
Marcus Delling
Harborline Builders Inc.
Licensed General Contractors
858-471-6093

Contact Information for Business Card

Use the flyer uploaded and website www.brightoakbuilders.com for inspiration. List Our Services on Backside of business cards Marcus Delling Harborline Builders Inc. Licensed General Contractors 858-471-6093

```html
<!DOCTYPE html>
<html lang="en">
<head>
<meta charset="UTF-8">
<title>Harborline Builders – Business Card</title>
<link href="https://fonts.googleapis.com/css2?family=Montserrat:wght@400;500;700&display=swap" rel="stylesheet">
<style>
  :root {
    --backdrop: #5e4a36;
    --card-light: #ffffff;
    --card-dark: #2a2a2a;
    --ink: #111111;
    --ink-soft: #222222;
    --paper-text: #f2f2f2;
    --rule: #444444;
  }
  * { margin: 0; padding: 0; box-sizing: border-box; }
  html, body {
    width: 900px; height: 1200px; overflow: hidden;
    background: var(--backdrop);
    font-family: "Montserrat", Arial, sans-serif;
  }
  .card {
    position: absolute;
    border-radius: 22px;
    box-shadow: 0 10px 24px rgba(0,0,0,0.35);
  }
  .card-front { left: 80px; top: 131px; width: 742px; height: 440px; background: var(--card-light); color: var(--ink); }
  .card-back { left: 78px; top: 638px; width: 744px; height: 440px; background: var(--card-dark); color: var(--paper-text); }

  .holder { position: absolute; right: 439px; top: 212px; text-align: right; }
  .holder-name { font-weight: 700; font-size: 27px; line-height: 32px; letter-spacing: -0.2px; }
  .holder-title { font-weight: 500; font-size: 15.5px; line-height: 18px; color: var(--ink-soft); }

  .divider { position: absolute; left: 326px; top: 186px; width: 1.5px; height: 118px; background: var(--rule); }

  .contact-list { position: absolute; left: 338px; top: 188px; list-style: none; }
  .contact-item { display: flex; align-items: center; height: 29px; font-size: 15.5px; font-weight: 500; }
  .contact-item svg { width: 16px; height: 16px; margin-right: 17px; fill: var(--ink); }
  .license { position: absolute; left: 340px; top: 290px; font-size: 15.5px; font-weight: 500; }

  .brand { position: absolute; left: 40px; top: 270px; width: 310px; text-align: center; }
  .brand-name { font-weight: 500; font-size: 25px; letter-spacing: 1.5px; text-transform: uppercase; color: var(--paper-text); }

  .services { position: absolute; left: 396px; top: 112px; }
  .services-title {
    display: inline-block; font-weight: 700; font-size: 21px;
    padding-bottom: 4px; border-bottom: 1.5px solid var(--paper-text);
  }
  .service-list { list-style: none; margin-top: 8px; }
  .service-item { position: relative; padding-left: 19px; font-size: 15.5px; line-height: 24px; font-weight: 500; }
  .service-item::before {
    content: ""; position: absolute; left: 3px; top: 10px;
    width: 5px; height: 5px; border-radius: 50%; background: var(--paper-text);
  }
</style>
</head>
<body>

<section class="card card-front">
  <div class="holder">
    <p class="holder-name">Marcus Delling</p>
    <p class="holder-title">Managing Director</p>
  </div>
  <div class="divider"></div>
  <ul class="contact-list">
    <li class="contact-item">
      <svg viewBox="0 0 16 16" aria-hidden="true"><path d="M1 5c0-2 3-3 7-3s7 1 7 3v1h-4V5H5v1H1z"/><path d="M3 7h10l1 7H2zM8 9a2 2 0 1 0 0 4 2 2 0 0 0 0-4z"/></svg>
      858-471-6093
    </li>
    <li class="contact-item">
      <svg viewBox="0 0 16 16" aria-hidden="true"><path d="M1 3h14v1.5L8 9 1 4.5z"/><path d="M1 6l7 4.5L15 6v7H1z"/></svg>
      info@brightoakbuilders.com
    </li>
    <li class="contact-item">
      <svg viewBox="0 0 16 16" aria-hidden="true"><circle cx="8" cy="8" r="7"/><path d="M5 4c1 1 2 1 2 2s-2 1-2 3 2 2 2 4M10 3c0 2 2 2 2 4s-2 2-1 4" stroke="#fff" stroke-width="1.3" fill="none"/></svg>
      www.brightoakbuilders.com
    </li>
  </ul>
  <p class="license">CSLB Licensed No. #1084652</p>
</section>

<section class="card card-back">
  <div class="brand">
    <p class="brand-name">Harborline Builders</p>
  </div>
  <div class="services">
    <h2 class="services-title">Our Services</h2>
    <ul class="service-list">
      <li class="service-item">Remodel: Kitchen &amp; Bath</li>
      <li class="service-item">Painting: Interior &amp; Exterior</li>
      <li class="service-item">Flooring: Carpet, Vinyl, Wood</li>
      <li class="service-item">Window: Door Replacement</li>
      <li class="service-item">Plumbing: Repair &amp; Upgrades</li>
      <li class="service-item">Energy Efficienct Upgrades</li>
      <li class="service-item">Deck &amp; Patio consturction</li>
      <li class="service-item">Water &amp; Mold Damage</li>
      <li class="service-item">Garage Renovation</li>
    </ul>
  </div>
</section>

</body>
</html>
```